Satchel & Sundial needs new business card design

I need a new business card design. I'm looking for out-of-the-box design which represents the freedom of being a location independent entrepreneur.
I offer coaching, retreats and trips.
I would like to see designs with and without the photo.
Colors I use are black (#000000), green (#25A796) and brown (#D7C38C)
Website satchelandsundial.example

Target Market(s)

location independent entrepreneurs, digital nomads, people looking to swap the 9 to 5 for a lifestyle business

Industry/Entity Type

Business

Contact Information for Business Card

Dorota Falkner
Your Lifestyle Business Coach, Retreat & Trip Leader
http://satchelandsundial.example
hello@satchelandsundial.example
Live a life you don't need a holiday from

Font styles to use
Serif
Sans Serif

Requirements
Must have
• One side should contain only the logo. I would also consider having the "Live a life you don't need a holiday from" on that side too (depending on how it looks)
• Please show both sides on the designs.

```html
<!DOCTYPE html>
<html lang="en">
<head>
<meta charset="utf-8">
<title>Satchel &amp; Sundial — Business Card</title>
<link rel="stylesheet" href="https://fonts.googleapis.com/css2?family=Bebas+Neue&display=swap">
<style>
  :root {
    --ink: #000000;
    --green: #25A796;
    --sand: #D7C38C;
    --backdrop: #1d1d1d;
    --paper: #ffffff;
  }
  * { margin: 0; padding: 0; box-sizing: border-box; }
  html, body {
    width: 1200px;
    height: 987px;
    overflow: hidden;
    background: var(--backdrop);
  }
  .canvas {
    position: relative;
    width: 1200px;
    height: 987px;
    font-family: "Bebas Neue", "Arial Narrow", sans-serif;
  }
  .card {
    position: absolute;
    left: 293px;
    width: 615px;
    height: 352px;
  }
  .card__frame {
    position: absolute;
    inset: 11px;
    border: 4px solid;
  }
  .card--front { top: 130px; background: var(--green); color: var(--paper); }
  .card--front .card__frame { border-color: var(--sand); }
  .card--back { top: 505px; background: var(--sand); }
  .card--back .card__frame { border-color: var(--green); }

  .line {
    position: absolute;
    left: 0;
    right: 0;
    text-align: center;
    line-height: 1;
    white-space: nowrap;
  }
  .social {
    position: absolute;
    top: 52px;
    left: 0;
    right: 0;
    display: flex;
    justify-content: center;
    gap: 16px;
  }
  .social__dot {
    width: 18px;
    height: 18px;
    border-radius: 50%;
    background: var(--paper);
  }
  .name { top: 121px; font-size: 40px; letter-spacing: 0.5px; }
  .role { font-size: 22px; }
  .role--coach { top: 166px; }
  .role--leader { top: 196px; }
  .contact { top: 262px; font-size: 15px; letter-spacing: 0.2px; }
  .contact__sep { padding: 0 6px; }
  .tagline { top: 285px; font-size: 19px; }

  .brand {
    position: absolute;
    inset: 0;
    display: flex;
    align-items: center;
    justify-content: center;
    gap: 14px;
    color: var(--ink);
    font-size: 64px;
    letter-spacing: 1px;
  }
  .brand__mark {
    width: 22px;
    height: 22px;
    border-radius: 50%;
    background: var(--green);
  }
</style>
</head>
<body>
<main class="canvas">
  <section class="card card--front" aria-label="Business card front">
    <div class="card__frame"></div>
    <div class="social" aria-label="Social media profiles">
      <span class="social__dot"></span>
      <span class="social__dot"></span>
      <span class="social__dot"></span>
    </div>
    <h1 class="line name">Dorota Falkner</h1>
    <p class="line role role--coach">Your Lifestyle Business Coach</p>
    <p class="line role role--leader">Retreat &amp; Trip Leader</p>
    <p class="line contact">hello@satchelandsundial.example<span class="contact__sep">|</span>www.satchelandsundial.example</p>
    <p class="line tagline">Live a life you don't need a holiday from</p>
  </section>

  <section class="card card--back" aria-label="Business card back">
    <div class="card__frame"></div>
    <div class="brand">
      <span class="brand__mark"></span>
      <span class="brand__name">Satchel &amp; Sundial</span>
    </div>
  </section>
</main>
</body>
</html>
```